VELTAR WEBSITE

need to create a new website for VELTAR ltd
the company deals with all aspects of safety products & safety wear
we need a simple website to show
ideas can be taken from following website whose products we shall distribute in kenya
www.kwr.co.uk
www.dorvik.eu
www.brimtoolsupplyco.com
www.gardvalewerks.co.za

we need following tabs
1) home - basic company information
2) products - broken down to following categories ie gloves, head protection, ear protection, mouth protection, foot protection
3) contacts

the company profile is a reputable company dealing with all aspects of safety, HSE (health and safety equipment), and PPE (personal protective equipment)

the website should have the dorvik logo for which we are an authorized distributor.
the dorvi industrial range writeup can be picked from their website
Updates

Dear Designers, i shall be able to choose a final design in 2 weeks, sorry i have not been able to finalise this due to a personal reason

Target Market(s)

the buyers are all types of industry who care for their employees safety

Industry/Entity Type

Industrial

Requirements
Must have
• clean look, fresh look, user freindly
Nice to have
• clear images, quick links etc

```html
<!DOCTYPE html>
<html lang="en">
<head>
<meta charset="utf-8">
<title>VELTAR – Safety &amp; Industrial Products</title>
<link href="https://fonts.googleapis.com/css2?family=Open+Sans:wght@400;600;700&display=swap" rel="stylesheet">
<style>
:root{
  --yellow:#f2b705;
  --navy:#1b2a3a;
  --ink:#3a3a3a;
  --muted:#8c8c8c;
  --page:#f6f6f6;
  --line:#dcdcdc;
  --footer:#4b4b4b;
  --footer-dark:#3b3b3b;
  --footer-text:#d8d8d8;
}
*{margin:0;padding:0;box-sizing:border-box}
html,body{width:800px;height:1200px;overflow:hidden}
body{font-family:'Open Sans',Arial,sans-serif;background:var(--page);color:var(--ink);position:relative}
.abs{position:absolute}
.topbar{top:0;left:0;width:800px;height:5px;background:var(--navy)}
.header{top:5px;left:0;width:800px;height:93px;background:var(--page)}
.brand{left:80px;top:37px;display:flex;align-items:center;gap:8px}
.brand-mark{width:18px;height:18px;background:var(--yellow)}
.brand-name{font-size:26px;font-weight:700;color:var(--navy);letter-spacing:1px}
.nav a{position:absolute;top:48px;font-size:10.5px;color:#666;text-decoration:none}
.nav .active-bg{position:absolute;left:363px;top:0;width:61px;height:93px;background:#e3e3e3;border-bottom:3px solid var(--yellow)}
.nav .caret{position:absolute;left:389px;top:87px;width:0;height:0;border-left:4px solid transparent;border-right:4px solid transparent;border-bottom:4px solid var(--yellow)}
.nav a.active{color:#222}
.hero{top:98px;left:0;width:800px;height:292px;background:linear-gradient(90deg,#181818 0%,#2a2a2a 45%,#4a4a4a 70%,#6c6c6c 100%)}
.hero-photo{position:absolute;right:0;top:0;width:420px;height:292px;background:radial-gradient(ellipse at 60% 55%,#8a8a8a 0%,#4d4d4d 50%,rgba(40,40,40,0) 80%),radial-gradient(ellipse at 65% 12%,#d9b20c 0%,rgba(217,178,12,0) 40%)}
.hero h1{position:absolute;left:87px;top:80px;font-size:20px;font-weight:400;color:#fff;line-height:22px}
.hero h1 b{color:var(--yellow);font-weight:600}
.hero h1 .y{color:var(--yellow)}
.hero p{position:absolute;left:88px;top:144px;width:270px;font-size:10px;line-height:12px;color:#eee}
.hero .more{position:absolute;left:88px;top:199px;font-size:10px;color:#fff;text-decoration:underline}
.dots{position:absolute;left:96px;top:268px;display:flex;gap:3px}
.dots i{width:8px;height:8px;border-radius:50%;background:#fff}
.dots i:first-child{background:var(--yellow)}
.feature{width:202px;height:94px;top:452px;background:#fafafa;border:1px solid var(--line);text-align:center}
.feature h3{margin-top:24px;font-size:12px;font-weight:400;color:#333}
.feature p{margin-top:6px;padding:0 22px;font-size:8.5px;line-height:12px;color:var(--muted)}
.feature.hot{background:var(--yellow);border-color:var(--yellow);box-shadow:3px 4px 5px rgba(0,0,0,.2)}
.feature.hot h3,.feature.hot p{color:#fff}
.feature .ic{position:absolute;left:80px;top:-31px;width:42px;height:42px}
.section-title{font-size:13.5px;font-weight:400;color:#444;background:var(--page);padding-right:8px;position:absolute}
.rule{height:1px;background:var(--line)}
.product{top:618px;width:147px}
.product .pic{height:109px}
.product h4{margin-top:9px;text-align:center;font-size:11px;font-weight:400;color:#444}
.product span{display:block;text-align:center;font-size:8px;color:var(--muted)}
.product .bar{margin:6px 2px 0;height:2px;background:#cfcfcf}
.product.sel .bar{background:var(--yellow)}
.welcome h2{font-size:14.5px}
.welcome h2 em{font-style:normal;color:var(--yellow)}
.body-copy{font-size:8.5px;line-height:12.2px;color:var(--muted)}
.btn{background:var(--navy);color:#fff;font-size:8.5px;display:flex;align-items:center;justify-content:center;border-radius:1px}
.field{left:564px;width:149px;background:#fff;border:1px solid #e2e2e2;font-size:7px;color:#999;padding:4px 7px}
.footer{top:969px;left:0;width:800px;height:181px;background:var(--footer)}
.footer h5{position:absolute;top:35px;font-size:10.5px;font-weight:400;color:#eee}
.footer .list{position:absolute;top:63px;font-size:8px;line-height:13.5px;color:var(--footer-text)}
.footer .list a{display:block;color:var(--footer-text);text-decoration:underline}
.footer .fline{position:absolute;height:1px;background:#5c5c5c}
.social{position:absolute;top:63px;width:21px;height:21px;border-radius:2px}
.news{position:absolute;left:533px;top:121px;width:177px;height:23px;background:#6a6a6a;border:2px solid #5a5a5a;border-radius:2px}
.news span{position:absolute;left:7px;top:5px;font-size:7.5px;font-style:italic;color:#bbb}
.news b{position:absolute;right:1px;top:1px;width:54px;height:17px;background:var(--yellow);font-size:8.5px;font-weight:400;color:#222;display:flex;align-items:center;justify-content:center}
.bottom{top:1150px;left:0;width:800px;height:50px;background:var(--footer-dark)}
.bottom nav{position:absolute;left:88px;top:19px;display:flex;gap:11px;font-size:8.5px;color:#ddd}
.bottom small{position:absolute;right:86px;top:19px;font-size:8.5px;color:#ddd}
</style>
</head>
<body>
<div class="abs topbar"></div>
<header class="abs header">
  <div class="abs brand"><span class="brand-mark"></span><span class="brand-name">VELTAR</span></div>
  <nav class="nav">
    <span class="active-bg"></span><span class="caret"></span>
    <a class="active" style="left:379px">Home</a>
    <a style="left:436px">About Us</a>
    <a style="left:507px">Our Products</a>
    <a style="left:601px">Agencies</a>
    <a style="left:670px">Contact Us</a>
  </nav>
</header>

<section class="abs hero">
  <div class="hero-photo" role="img" aria-label="Black and white photo of a worker wearing a yellow hard hat, seen in profile"></div>
  <h1><b>VELTAR</b> Specialized Protective<br><span class="y">&amp;</span> Industrial <b>Products</b></h1>
  <p>Lorem ipsum dolor sit amet, consectetur adipisicing elit, sed do eiusmod tempor incididunt ut labore et dolore magna aliqua...</p>
  <a class="more">READ MORE</a>
  <div class="dots"><i></i><i></i><i></i><i></i></div>
</section>

<div class="abs feature" style="left:86px">
  <svg class="ic" viewBox="0 0 42 42"><circle cx="21" cy="21" r="21" fill="#f2b705"/><circle cx="21" cy="21" r="18" fill="none" stroke="#fff" stroke-width="1"/><path d="M13 28 L25 16 M17 14 L28 27" stroke="#fff" stroke-width="3" stroke-linecap="round"/><path d="M24 13 l5 0 l0 5" stroke="#fff" stroke-width="2" fill="none"/></svg>
  <h3>TOOL DIVISION</h3>
  <p>Sed ut perspiciatis unde omnis iste natus error sit voluptatem accusan-tium doloremque laudantium</p>
</div>
<div class="abs feature hot" style="left:299px">
  <svg class="ic" viewBox="0 0 42 42"><circle cx="21" cy="21" r="21" fill="#fff"/><circle cx="21" cy="21" r="17" fill="#4a4a4a"/><path d="M11 25 Q12 14 22 14 Q31 15 31 25 Z" fill="#fff"/><rect x="9" y="25" width="24" height="2.5" fill="#fff"/></svg>
  <h3>SAFETY DIVISION</h3>
  <p>Sed ut perspiciatis unde omnis iste natus error sit voluptatem accusan-tium doloremque laudantium</p>
</div>
<div class="abs feature" style="left:513px">
  <svg class="ic" viewBox="0 0 42 42"><circle cx="21" cy="21" r="21" fill="#f2b705"/><circle cx="21" cy="21" r="16" fill="none" stroke="#fff" stroke-width="2"/><path d="M15 17 Q15 14 17 14 L18 17 L16.5 18.5 Q18 23 23.5 25.5 L25 24 L28 25 Q28 27 25 27.5 Q17 26 15 17 Z" fill="#fff"/></svg>
  <h3 style="margin-top:20px">CONTACT US</h3>
  <p>Sed ut perspiciatis unde omnis iste natus error sit voluptatem accusan-tium doloremque laudantium</p>
</div>

<div class="abs rule" style="left:88px;top:594px;width:600px"></div>
<h2 class="section-title" style="left:88px;top:585px">Our Products</h2>
<svg class="abs" style="left:694px;top:589px" width="22" height="12" viewBox="0 0 22 12"><path d="M6 1 L1 6 L6 11" stroke="#333" stroke-width="1.6" fill="none"/><path d="M15 1 L20 6 L15 11" stroke="#f2b705" stroke-width="1.6" fill="none"/></svg>

<div class="abs product" style="left:87px"><div class="pic" role="img" aria-label="Photo of a worker in a blue hard hat and safety glasses" style="background:linear-gradient(135deg,#8aa3b8,#3f5f86 55%,#7a7f86)"></div><h4>Head Protection</h4><span>Lorem ipsum</span><div class="bar"></div></div>
<div class="abs product sel" style="left:247px"><div class="pic" role="img" aria-label="Photo of hands pulling on blue protective gloves" style="background:linear-gradient(135deg,#c9b79a,#6fb0d8 50%,#d9c3a4)"></div><h4>Hand Protection</h4><span>Lorem Ipsum</span><div class="bar"></div></div>
<div class="abs product" style="left:407px"><div class="pic" role="img" aria-label="Photo of a pair of worn work boots" style="background:linear-gradient(180deg,#f2c96a,#b5763a 55%,#5a3a22)"></div><h4>Foot Protection</h4><span>Lorem Ipsum</span><div class="bar"></div></div>
<div class="abs product" style="left:566px"><div class="pic" role="img" aria-label="Photo of clear mouth guards on a wooden surface" style="background:linear-gradient(135deg,#9c6a35,#c99a62 50%,#7a4f28)"></div><h4>Mouth Protection</h4><span>Lorem Ipsum</span><div class="bar"></div></div>

<div class="abs rule" style="left:88px;top:800px;width:466px"></div>
<h2 class="section-title welcome" style="left:88px;top:789px;font-size:14.5px">Welcome To <em style="font-style:normal;color:var(--yellow)">VELTAR</em> Specialized</h2>
<p class="abs body-copy" style="left:88px;top:814px;width:462px">Lorem ipsum dolor sit amet, consectetur adipisicing elit, sed do eiusmod tempor incididunt ut labore et dolore magna aliqua. Ut enim ad minim veniam, quis nostrud exercitation ullamco laboris nisi ut aliquip ex ea commodo consequat. Duis aute irure dolor in reprehenderit in voluptate velit esse cillum dolore eu fugiat nulla pariatur. Excepteur sint occaecat cupidatat non proident, sunt in culpa qui officia deserunt mollit anim id est laborum.</p>
<p class="abs body-copy" style="left:88px;top:876px;width:462px">Lorem ipsum dolor sit amet, consectetur adipisicing elit, sed do eiusmod tempor incididunt ut labore et dolore magna aliqua quis nostrud exercitation ullamco laboris nisi ut aliquip ex ea commodo consequat.</p>
<a class="abs btn" style="left:87px;top:917px;width:59px;height:20px">Read More</a>

<div class="abs rule" style="left:566px;top:800px;width:154px"></div>
<h2 class="section-title" style="left:566px;top:789px;font-size:14.5px">Get A Quote</h2>
<div class="abs field" style="top:818px;height:17px">Enter your name...</div>
<div class="abs field" style="top:843px;height:17px">Enter your email...</div>
<div class="abs field" style="top:867px;height:42px">Enter your comment...</div>
<a class="abs btn" style="left:654px;top:917px;width:59px;height:20px">Submit</a>

<footer class="abs footer">
  <h5 style="left:86px">Contact Info</h5><div class="fline" style="left:146px;top:43px;width:43px"></div>
  <div class="list" style="left:87px"><a>lorem ipsum</a><a>dolor sit amet 106</a><a>1404 consecteture</a><a>adipisicing elit</a><a>eMail: info@veltar-ltd.com</a><a>Phone: +800-555-0192</a></div>
  <h5 style="left:224px">About Us</h5><div class="fline" style="left:272px;top:43px;width:93px"></div>
  <p class="list" style="left:224px;width:145px;line-height:14.6px">Lorem ipsum dolor sit amet, consectetur adipisicing elit, sed do eiusmod tempor incididunt ut labore et dolore magna aliqua. Ut enim ad minim veniam.</p>
  <h5 style="left:397px">Company Info</h5><div class="fline" style="left:468px;top:43px;width:33px"></div>
  <div class="list" style="left:397px"><a>Lorem ipsum</a><a>dolor sit amet</a><a>consectetur</a><a>adipsicing elit</a></div>
  <h5 style="left:533px">Stay updates on our Socail Network</h5>
  <span class="social" style="left:534px;background:#3b5ea8"></span>
  <span class="social" style="left:564px;background:#5aaee0"></span>
  <span class="social" style="left:594px;background:#2a7ab5"></span>
  <h5 style="left:533px;top:105px">Join Our Newsletter</h5><div class="fline" style="left:632px;top:113px;width:78px"></div>
  <div class="news"><span>Enter your email address</span><b>Subscribe</b></div>
</footer>
<div class="abs bottom">
  <nav><span>Home</span><span>About Us</span><span>Our Products</span><span>Agencies</span><span>Contact Us</span></nav>
  <small>© Copyrights 2013 All rights Reserved</small>
</div>
</body>
</html>
```